Business Card for: Bramwell Financial Advisory Services Inc.

provide strategic financial advisory services to companies in the areas of corporate finance, mergers and acquisitions, executive coaching and strategic planning

Target Market(s)

Companies, banks, accountants, lawyers

Industry/Entity Type

High end business consulting in corporate finance, mergers and acquisitions, consulting

Contact Information for Business Card

Name of company, Name: xxxxxx xxxxxx , CEO, - phone number: 1-xxx-xxx-xxxx, - email address,

Requirements
Must have
• Must be professional and simple.
Nice to have
• simple, straight graphics, must give the impression that we are trustworthy, professional, competent
Should not have
• loud colors, loud design features

```html
<!DOCTYPE html>
<html lang="en">
<head>
<meta charset="utf-8">
<title>Bramwell Financial Advisory Services Inc. – Business Card</title>
<link rel="stylesheet" href="https://fonts.googleapis.com/css2?family=Roboto:wght@400;500&display=swap">
<style>
  :root {
    --bg: #3a3a3b;
    --card: #0f0f10;
    --gold: #c08f62;
    --gold-soft: #a97a52;
    --glow-a: rgba(150, 100, 60, 0.45);
    --glow-b: rgba(90, 58, 34, 0.25);
  }
  * { margin: 0; padding: 0; box-sizing: border-box; }
  html, body { width: 1200px; height: 694px; overflow: hidden; }
  body {
    background: var(--bg);
    font-family: "Roboto", Arial, sans-serif;
    color: var(--gold);
    position: relative;
  }
  .card {
    position: absolute;
    top: 204px;
    width: 500px;
    height: 286px;
    background: var(--card);
    border-radius: 26px;
    box-shadow: 0 18px 40px rgba(0, 0, 0, 0.45);
    overflow: hidden;
  }
  .card--front { left: 70px; }
  .card--back { left: 630px; }

  /* Brand lockup: one plain circle + wordmark in one weight */
  .brand {
    position: absolute;
    display: flex;
    align-items: center;
  }
  .brand__circle {
    border-radius: 50%;
    background: radial-gradient(circle at 45% 40%, var(--glow-a), var(--glow-b) 70%, transparent 100%);
    flex: none;
  }
  .brand__name {
    font-weight: 500;
    color: var(--gold);
    line-height: 1.05;
  }
  .brand__name span { display: block; }

  .card--front .brand { left: 120px; top: 60px; gap: 18px; }
  .card--front .brand__circle { width: 130px; height: 130px; }
  .card--front .brand__name { font-size: 20px; }
  .card--front .brand__name .brand__sub { font-size: 11px; margin-top: 3px; }

  .address {
    position: absolute;
    left: 0; right: 0;
    bottom: 40px;
    text-align: center;
    font-size: 13px;
    letter-spacing: 0.22em;
    color: var(--gold-soft);
  }

  /* Back */
  .card--back .brand { right: 26px; top: 30px; gap: 8px; }
  .card--back .brand__circle { width: 58px; height: 58px; }
  .card--back .brand__name { font-size: 11px; }
  .card--back .brand__name .brand__sub { font-size: 7px; margin-top: 2px; }

  .holder {
    position: absolute;
    left: 34px; top: 110px;
    color: var(--gold-soft);
  }
  .holder__name { font-size: 14px; font-weight: 500; }
  .holder__role { font-size: 12px; letter-spacing: 0.25em; margin-top: 2px; }

  .phone {
    position: absolute;
    left: 34px; top: 160px;
    color: var(--gold);
  }
  .phone__label { font-size: 12px; letter-spacing: 0.12em; color: var(--gold-soft); }
  .phone__number {
    font-size: 30px;
    font-weight: 500;
    letter-spacing: 0.45em;
    margin-top: 2px;
    white-space: nowrap;
  }

  .email {
    position: absolute;
    left: 34px; bottom: 30px;
    font-size: 12px;
    color: var(--gold-soft);
    line-height: 1.35;
  }
</style>
</head>
<body>
  <section class="card card--front" aria-label="Business card front">
    <div class="brand">
      <div class="brand__circle"></div>
      <div class="brand__name">
        <span>Bramwell</span>
        <span>Financial Advisory</span>
        <span class="brand__sub">Services Inc</span>
      </div>
    </div>
    <p class="address">address will come here, dummy for now</p>
  </section>

  <section class="card card--back" aria-label="Business card back">
    <div class="brand">
      <div class="brand__circle"></div>
      <div class="brand__name">
        <span>Bramwell</span>
        <span>Financial Advisory</span>
        <span class="brand__sub">Services Inc</span>
      </div>
    </div>
    <div class="holder">
      <p class="holder__name">Owner name</p>
      <p class="holder__role">CEO</p>
    </div>
    <div class="phone">
      <p class="phone__label">Phone -</p>
      <p class="phone__number">123 456 7890</p>
    </div>
    <p class="email">Email -<br>info@bramwellfinancial.com</p>
  </section>
</body>
</html>
```